Law Firm Header Revision

Task: Redesign my law firm Word document header (modern, succinct, logo-first, easy address updates)

I need you to revise and modernize my Microsoft Word document header for Law Office of Bram Holcott, PLLC. The result should look professional and clean on letters (including Letters of Protection), with the logo as the main focus and the text kept succinct.

Goals:
1. Create a modern, minimal header that feels premium and uncluttered.
Make the logo the most visually dominant element.
Reduce the visual weight of the contact/address block so it doesn’t distract from the document.
Make the address easy to change later (I’m moving offices soon) while keeping the same header design.

2. Content to include (keep all info accurate):
Law Office of Bram Holcott, PLLC
615 Pemberly St. Ste #300-214, Houston, TX 77002
Office: 832.555.0143
Direct: 713.555.0187
Fax: 832.555.0129
Bholcottlaw.com

3. Layout requirements:
Provide 3 header style options:
Logo left + contact info right
Centered logo + single concise contact line below
Logo left + firm name prominent + minimal contact line
The primary line near the logo should be minimal (preferably website + main office phone).
The address should be easy to update in one place without redesigning the header. Prefer either:
Move the full address to the footer, or
Put the address in a single dedicated line/block so I can edit it once and keep the layout unchanged.
4. Build constraints:
Must be achievable using standard Microsoft Word tools only (header/footer, tables, alignment, fonts, spacing). No advanced graphics software.
Provide exact header text, plus step-by-step Word instructions for each option:
Font recommendations + sizes
Alignment
Spacing
Table setup (if used)
How to keep it consistent across pages

5. Deliverable:
For each of the 3 options, provide:
The exact header content (with line breaks)
Formatting specs (fonts, sizes, spacing)
Word build steps so I can recreate it reliably and keep the logo as the focal point.

```html
<!DOCTYPE html>
<html lang="en">
<head>
<meta charset="utf-8">
<title>Bram Holcott Law – Header Options</title>
<link href="https://fonts.googleapis.com/css2?family=Lato:wght@400;700&display=swap" rel="stylesheet">
<style>
  :root {
    --navy: #0b1f33;
    --ink: #444a50;
    --muted: #6b7178;
    --hairline: #d5d9de;
    --charcoal: #1b1b1b;
    --paper: #ffffff;
  }
  html, body { margin: 0; padding: 0; overflow: hidden; background: var(--paper); }
  .sheet {
    position: relative; width: 927px; height: 1200px; overflow: hidden;
    background: var(--paper); font-family: "Lato", Arial, sans-serif; color: var(--ink);
  }
  .option { position: absolute; left: 0; width: 927px; }
  .option-1 { top: 0; height: 345px; }
  .option-2 { top: 350px; height: 345px; }
  .option-3 { top: 700px; height: 345px; }
  .divider { position: absolute; left: 32px; right: 32px; height: 1px; background: var(--hairline); }

  .mark-square { position: absolute; background: var(--navy); }
  .mark-name { position: absolute; margin: 0; font-weight: 700; color: var(--navy); white-space: nowrap; line-height: 1; }

  .contact-item { position: absolute; display: flex; align-items: center; font-size: 13.5px; color: var(--ink); }
  .icon-tile {
    width: 42px; height: 38px; background: var(--navy); flex: none;
    display: flex; align-items: center; justify-content: center;
  }
  .icon-tile svg { width: 24px; height: 24px; fill: none; stroke: #fff; stroke-width: 1.3; stroke-linecap: round; stroke-linejoin: round; }
  .contact-item .label { margin-left: 14px; line-height: 18px; }

  .contact-line { position: absolute; font-size: 12.5px; color: var(--ink); white-space: nowrap; }

  .spec { position: absolute; left: 32px; right: 32px; font-size: 10.5px; line-height: 14px; color: var(--ink); }
  .spec-label {
    font-weight: 700; font-size: 11px; letter-spacing: 1.5px; text-transform: uppercase;
    color: var(--navy); margin: 0 0 6px;
  }
  .spec-grid { display: grid; grid-template-columns: 240px 1fr; gap: 24px; }
  .spec-head { font-weight: 700; color: var(--navy); margin: 0 0 2px; }
  .spec-text { margin: 0; white-space: pre-line; }
  .spec ul { margin: 0; padding-left: 13px; }
  .spec li { margin: 0; }

  .foot-bar { position: absolute; left: 0; top: 1157px; }
  .foot-title { position: absolute; left: 31px; top: 1168px; color: #fff; font-size: 14px; }
  .foot-page { position: absolute; right: 33px; top: 1167px; color: #fff; font-size: 14px; }
</style>
</head>
<body>
<div class="sheet">

  <!-- Option 1: mark left, contact right -->
  <section class="option option-1">
    <div class="mark-square" style="left:32px; top:22px; width:100px; height:110px;" aria-hidden="true"></div>
    <h1 class="mark-name" style="left:150px; top:34px; font-size:44px;">BRAM HOLCOTT</h1>
    <div class="mark-name" style="left:152px; top:90px; font-size:24px; letter-spacing:14px;">LAW</div>

    <div class="contact-item" style="left:567px; top:18px;">
      <div class="icon-tile">
        <svg viewBox="0 0 26 26"><circle cx="13" cy="13" r="10"/><ellipse cx="13" cy="13" rx="4.5" ry="10"/><line x1="3" y1="13" x2="23" y2="13"/><path d="M5 7.5h16M5 18.5h16"/></svg>
      </div>
      <span class="label">Bholcottlaw.com</span>
    </div>
    <div class="contact-item" style="left:753px; top:18px;">
      <div class="icon-tile">
        <svg viewBox="0 0 26 26"><path d="M7 5l3 4-2 2c1 3 3 5 6 6l2-2 4 3-2 3c-7 0-13-6-13-13z"/><path d="M15 6a6 6 0 0 1 5 5M15 3a9 9 0 0 1 8 8"/></svg>
      </div>
      <span class="label">832.555.0143</span>
    </div>
    <svg style="position:absolute; left:0; top:0;" width="927" height="130" aria-hidden="true">
      <polygon points="545,72 927,72 927,112 524,112" fill="var(--navy)"/>
    </svg>

    <div class="spec" style="top:152px;">
      <p class="spec-label">Option 1 — Logo left + contact right</p>
      <div class="spec-grid">
        <div>
          <p class="spec-head">Header text</p>
          <p class="spec-text">[Logo]
Bholcottlaw.com   ·   832.555.0143

Footer (edit once):
615 Pemberly St. Ste #300-214, Houston, TX 77002
Direct 713.555.0187 · Fax 832.555.0129</p>
        </div>
        <div>
          <p class="spec-head">Formatting &amp; Word build</p>
          <ul>
            <li>Fonts: logo image 1.4" tall; contact Lato 10 pt, #444A50; footer Lato 9 pt.</li>
            <li>Table: Insert → Table 1×2 inside the header; column 1 = 4.2", column 2 = 2.8"; Borders → No Border; cell margins 0".</li>
            <li>Alignment: column 1 left, logo set In Line with Text; column 2 right, cell alignment Top Right.</li>
            <li>Spacing: 0 pt before / 0 pt after, single line; Header from Top 0.4".</li>
            <li>Band: Insert → Shapes → Parallelogram, fill #0B1F33, no outline, Behind Text, anchored in header.</li>
            <li>Address: one footer paragraph saved as a Quick Part named “Address” — change it once, layout stays.</li>
            <li>Consistency: keep Link to Previous on, Different First Page off; save as a .dotx template.</li>
          </ul>
        </div>
      </div>
    </div>
  </section>
  <div class="divider" style="top:345px;"></div>

  <!-- Option 2: centered mark + one contact line -->
  <section class="option option-2">
    <div class="mark-square" style="left:437px; top:12px; width:52px; height:52px;" aria-hidden="true"></div>
    <div class="mark-name" style="left:0; width:927px; text-align:center; top:72px; font-size:38px;">BRAM HOLCOTT LAW</div>
    <div class="contact-line" style="left:0; width:927px; text-align:center; top:120px; letter-spacing:0.5px;">Bholcottlaw.com  &nbsp;|&nbsp;  Office 832.555.0143</div>
    <div style="position:absolute; left:213px; width:500px; top:144px; height:1px; background:var(--navy);"></div>

    <div class="spec" style="top:158px;">
      <p class="spec-label">Option 2 — Centered logo + single contact line</p>
      <div class="spec-grid">
        <div>
          <p class="spec-head">Header text</p>
          <p class="spec-text">[Logo, centered]
Bholcottlaw.com  |  Office 832.555.0143

Footer (edit once, centered):
615 Pemberly St. Ste #300-214, Houston, TX 77002
Direct 713.555.0187 · Fax 832.555.0129</p>
        </div>
        <div>
          <p class="spec-head">Formatting &amp; Word build</p>
          <ul>
            <li>Fonts: logo image 1.0" tall; contact line Lato 9.5 pt, Font → Advanced → Spacing Expanded 0.5 pt.</li>
            <li>Alignment: Center both paragraphs (Ctrl+E); logo In Line with Text so it never drifts.</li>
            <li>Spacing: logo 0 pt before / 6 pt after; contact line 0 pt / 12 pt after.</li>
            <li>Rule: select contact line → Borders → Bottom Border, 0.75 pt, #0B1F33; indent 1.2" left and right.</li>
            <li>No table needed; use “ | ” with single spaces as the separator.</li>
            <li>Address: footer, Lato 8.5 pt, one line — the only place it appears.</li>
            <li>Consistency: save the contact paragraph as a “Header Contact” style and reuse it in every template.</li>
          </ul>
        </div>
      </div>
    </div>
  </section>
  <div class="divider" style="top:695px;"></div>

  <!-- Option 3: mark left + firm name + minimal line -->
  <section class="option option-3">
    <div class="mark-square" style="left:32px; top:14px; width:86px; height:94px;" aria-hidden="true"></div>
    <div class="mark-name" style="left:134px; top:24px; font-size:38px;">BRAM HOLCOTT</div>
    <div class="mark-name" style="left:136px; top:72px; font-size:20px; letter-spacing:12px;">LAW</div>
    <div style="position:absolute; left:440px; top:22px; width:1px; height:78px; background:var(--hairline);"></div>
    <div class="mark-name" style="left:462px; top:34px; font-size:20px;">Law Office of Bram Holcott, PLLC</div>
    <div class="contact-line" style="left:462px; top:68px;">Bholcottlaw.com  ·  832.555.0143</div>
    <div style="position:absolute; left:32px; right:32px; top:122px; height:3px; background:var(--navy);"></div>

    <div class="spec" style="top:140px;">
      <p class="spec-label">Option 3 — Logo left + firm name + minimal line</p>
      <div class="spec-grid">
        <div>
          <p class="spec-head">Header text</p>
          <p class="spec-text">[Logo]  Law Office of Bram Holcott, PLLC
           Bholcottlaw.com  ·  832.555.0143

Footer (edit once):
615 Pemberly St. Ste #300-214, Houston, TX 77002
Direct 713.555.0187 · Fax 832.555.0129</p>
        </div>
        <div>
          <p class="spec-head">Formatting &amp; Word build</p>
          <ul>
            <li>Table: Insert → Table 1×2; column 1 = 3.6" (logo), column 2 = 3.4"; No Border; cell margins 0".</li>
            <li>Fonts: logo image 1.2" tall; firm name Lato Bold 16 pt #0B1F33; contact line Lato 9 pt #444A50.</li>
            <li>Alignment: column 1 left; column 2 left with a 0.75 pt light grey left cell border; both cells Center vertically.</li>
            <li>Spacing: firm name 0 pt before / 4 pt after; contact line 0 pt / 0 pt; Header from Top 0.4".</li>
            <li>Rule: empty paragraph under the table → Borders → Bottom Border, 2.25 pt, #0B1F33.</li>
            <li>Address, Direct and Fax stay in the footer Quick Part — update once for the office move.</li>
            <li>Consistency: select the header → Header → Save Selection to Header Gallery; insert it on every template.</li>
          </ul>
        </div>
      </div>
    </div>
  </section>

  <!-- Shared footer: address lives here only -->
  <footer>
    <div class="contact-item" style="left:291px; top:1094px;">
      <div class="icon-tile">
        <svg viewBox="0 0 26 26"><path d="M13 24s-7-8-7-13a7 7 0 0 1 14 0c0 5-7 13-7 13z"/><circle cx="13" cy="11" r="2.6"/></svg>
      </div>
      <span class="label">615 Pemberly St. Ste #300-214,<br>Houston, TX 77002</span>
    </div>
    <div class="contact-item" style="left:572px; top:1094px;">
      <div class="icon-tile">
        <svg viewBox="0 0 26 26"><path d="M13 24V4M10 7l3-3 3 3"/><path d="M13 16c0-3-3-4-8-4M7 10l-2 2 2 2"/><path d="M13 16c0-3 3-4 8-4M19 10l2 2-2 2"/></svg>
      </div>
      <span class="label">713.555.0187</span>
    </div>
    <div class="contact-item" style="left:750px; top:1094px;">
      <div class="icon-tile">
        <svg viewBox="0 0 26 26"><rect x="3" y="8" width="4" height="15"/><rect x="7" y="10" width="16" height="13"/><rect x="10" y="3" width="10" height="7"/><path d="M11 14h1M14 14h1M17 14h1M11 17h1M14 17h1M17 17h1M11 20h1M14 20h1M17 20h1"/></svg>
      </div>
      <span class="label">832.555.0129</span>
    </div>

    <svg class="foot-bar" width="927" height="43" aria-hidden="true">
      <polygon points="0,0 614,0 592,43 0,43" fill="var(--navy)"/>
      <polygon points="622,0 927,0 927,43 600,43" fill="var(--charcoal)"/>
    </svg>
    <div class="foot-title">Letter of Protection</div>
    <div class="foot-page">Page 1</div>
  </footer>
</div>
</body>
</html>
```